The Copperline Collective's website for high impact furniture promotions

I am looking for a simple website. we are a promotional company that runs events for furniture stores to increase sales for short periods of time. i would like the website to have about 4 areas to explain our company. I would like it to be simple and user friendly. I would like a link to chatterbook and a contact section. I am attaching our logo that i would like somewhere large or possibly in the backround. I am open to different color schemes. I would like to convey fast paced, modern, reliable. I am open to all different styles and look forward to seeing whats out there. we are looking for a quick turn around, so if we see one that we like quick, we will pick that one thanks
Reason: looking for some really creative designs and want to give a fair amount of time to produce
Target Market(s)
Retail Furniture store owners
Industry/Entity Type
It Company
Number of Pages Required
1 page
Colors
Designer to choose colors to be used in the design.
Look and feel

```html
<!DOCTYPE html>
<html lang="en">
<head>
<meta charset="utf-8">
<title>The Copperline Collective — High Impact Furniture Promotions</title>
<link rel="stylesheet" href="https://fonts.googleapis.com/css2?family=Nunito:wght@400;600;700&family=Open+Sans:wght@400;600&display=swap">
<style>
  :root {
    --copper: #b8946a;
    --copper-dark: #8e6038;
    --copper-deep: #6b4424;
    --ink: #1f1f1f;
    --ink-soft: #7a7a7a;
    --night: #1d1a19;
    --line: #d9d9d9;
    --white: #ffffff;
  }
  * { box-sizing: border-box; margin: 0; padding: 0; }
  html, body { width: 1200px; height: 2192px; overflow: hidden; }
  body { position: relative; background: var(--white); font-family: "Open Sans", Arial, sans-serif; color: var(--ink); }

  /* Hero */
  .hero { position: absolute; left: 0; top: 0; width: 1200px; height: 680px; overflow: hidden; }
  .hero-photo {
    position: absolute; inset: 0;
    background:
      radial-gradient(ellipse at 75% 20%, rgba(240,190,110,.75), transparent 45%),
      radial-gradient(ellipse at 20% 40%, rgba(150,120,110,.6), transparent 50%),
      linear-gradient(180deg, #8a6e66 0%, #a58a7a 35%, #c2a792 60%, #9c8174 100%);
  }
  .hero-shade { position: absolute; inset: 0; background: rgba(40,25,20,.25); }
  .hero-curve { position: absolute; left: 0; top: 530px; width: 1200px; height: 150px; }

  .brand { position: absolute; left: 120px; top: 44px; display: flex; align-items: center; gap: 14px; }
  .brand-dot { width: 58px; height: 58px; border-radius: 50%; background: var(--white); }
  .brand-name { font-family: "Nunito", Arial, sans-serif; font-weight: 600; font-size: 22px; color: var(--white); letter-spacing: 1px; line-height: 1.15; width: 220px; }

  .main-nav { position: absolute; left: 484px; top: 62px; display: flex; gap: 27px; }
  .main-nav a { font-family: "Open Sans", Arial, sans-serif; font-size: 15.5px; color: var(--white); text-decoration: none; position: relative; padding-bottom: 8px; }
  .main-nav a.is-active::after { content: ""; position: absolute; left: 0; right: 0; bottom: -2px; height: 2px; background: var(--copper); }

  .hero-arrow { position: absolute; top: 296px; width: 26px; height: 58px; }
  .hero-arrow.prev { left: 97px; }
  .hero-arrow.next { left: 1081px; }

  .hero-title { position: absolute; left: 0; width: 1200px; top: 306px; text-align: center; font-family: "Nunito", Arial, sans-serif; font-weight: 700; font-size: 42px; color: var(--white); letter-spacing: .5px; }
  .hero-sub { position: absolute; left: 0; width: 1200px; top: 364px; text-align: center; font-family: "Nunito", Arial, sans-serif; font-weight: 400; font-size: 25px; color: var(--white); letter-spacing: .5px; }

  .hero-badge { position: absolute; left: 560px; top: 625px; width: 80px; height: 80px; border-radius: 50%; background: var(--copper); border: 5px solid var(--white); box-shadow: 0 0 0 2px var(--copper); }

  /* Feature cards */
  .features { position: absolute; top: 726px; left: 121px; width: 962px; height: 380px; }
  .card { position: absolute; top: 0; width: 307px; height: 379px; background: var(--white); border: 1px solid #dcdcdc; box-shadow: 0 1px 3px rgba(0,0,0,.18); text-align: center; }
  .card:nth-child(1) { left: 0; }
  .card:nth-child(2) { left: 325px; }
  .card:nth-child(3) { left: 655px; }
  .card-photo { height: 186px; margin: 1px; }
  .card-photo.showroom { background: linear-gradient(135deg, #6e4a3c, #c9b7a6 55%, #8a3d2e); }
  .card-photo.gallery { background: linear-gradient(160deg, #4b4a3d, #b3a068 50%, #6d6a58); }
  .card-photo.dining { background: linear-gradient(170deg, #5a5f6c, #b99a7a 55%, #d7d2cd); }
  .card-title { margin-top: 22px; font-family: "Nunito", Arial, sans-serif; font-weight: 400; font-size: 22px; color: var(--ink); letter-spacing: .5px; }
  .card-text { margin: 10px auto 0; width: 250px; font-size: 13px; line-height: 20px; color: var(--ink-soft); }
  .btn-pill { display: inline-block; margin-top: 18px; width: 134px; height: 39px; line-height: 39px; border-radius: 20px; background: var(--copper); color: var(--white); font-family: "Nunito", Arial, sans-serif; font-size: 13.5px; font-weight: 600; letter-spacing: .4px; text-decoration: none; }

  /* Mission */
  .mission { position: absolute; top: 1159px; left: 0; width: 1200px; height: 446px; }
  .mission-panel { position: absolute; left: 0; top: 0; width: 601px; height: 446px; background: var(--copper-dark); }
  .mission-photo { position: absolute; left: 601px; top: 0; width: 599px; height: 446px;
    background:
      radial-gradient(circle at 60% 20%, rgba(255,230,220,.8), transparent 35%),
      radial-gradient(circle at 85% 45%, rgba(230,160,170,.55), transparent 40%),
      linear-gradient(180deg, #6b4a66 0%, #8b5a5a 45%, #3a2220 100%); }
  .mission-notch { position: absolute; left: 600px; top: 1354px; width: 0; height: 0; border-top: 20px solid transparent; border-bottom: 20px solid transparent; border-left: 20px solid var(--copper-dark); }
  .mission-title { position: absolute; left: 117px; top: 92px; font-family: "Nunito", Arial, sans-serif; font-weight: 400; font-size: 30px; color: var(--white); letter-spacing: .6px; }
  .mission-text { position: absolute; left: 115px; width: 425px; font-size: 13.5px; line-height: 20.5px; color: #f1e4d6; }
  .mission-text.first { top: 146px; }
  .mission-text.second { top: 223px; }
  .btn-outline { position: absolute; left: 114px; top: 327px; width: 137px; height: 41px; line-height: 37px; border: 2px solid var(--white); border-radius: 21px; text-align: center; color: var(--white); font-family: "Nunito", Arial, sans-serif; font-size: 14px; font-weight: 600; letter-spacing: .4px; text-decoration: none; }

  /* Contact */
  .contact { position: absolute; top: 1605px; left: 0; width: 1200px; height: 459px;
    background:
      radial-gradient(ellipse at 30% 20%, rgba(90,60,45,.45), transparent 55%),
      radial-gradient(ellipse at 80% 60%, rgba(70,50,45,.4), transparent 50%),
      linear-gradient(180deg, #262220, #181615); }
  .contact-title { position: absolute; left: 0; width: 1200px; top: 54px; text-align: center; font-family: "Nunito", Arial, sans-serif; font-weight: 400; font-size: 28px; color: var(--white); letter-spacing: .6px; }
  .field { position: absolute; border: 1px solid #8a8a8a; background: transparent; color: #cfcfcf; font-family: "Open Sans", Arial, sans-serif; font-size: 14px; padding: 0 15px; }
  .field.col-a { left: 205px; width: 395px; }
  .field.col-b { left: 609px; width: 397px; }
  .field.row-1 { top: 115px; height: 43px; line-height: 41px; }
  .field.row-2 { top: 168px; height: 43px; line-height: 41px; }
  .field.message { left: 205px; width: 801px; top: 223px; height: 110px; padding-top: 12px; }
  .btn-submit { position: absolute; left: 528px; top: 358px; width: 169px; height: 41px; line-height: 41px; background: var(--copper); color: var(--white); text-align: center; font-family: "Nunito", Arial, sans-serif; font-size: 16px; font-weight: 600; letter-spacing: .4px; }

  /* Footer */
  .site-footer { position: absolute; top: 2064px; left: 0; width: 1200px; height: 128px; background: var(--white); }
  .footer-nav { position: absolute; left: 127px; top: 40px; display: flex; gap: 30px; }
  .footer-nav a { font-size: 15px; color: var(--ink); text-decoration: none; }
  .footer-legal { position: absolute; left: 127px; top: 75px; font-size: 12.5px; color: #444; }
  .social { position: absolute; right: 126px; top: 30px; display: flex; align-items: center; gap: 10px; text-decoration: none; }
  .social-label { font-size: 13px; color: var(--ink); }
  .social-ring { width: 37px; height: 37px; border-radius: 50%; border: 1.5px solid var(--ink); }
</style>
</head>
<body>

<header class="hero">
  <div class="hero-photo" role="img" aria-label="Blurred photo of a busy furniture trade show hall with shoppers"></div>
  <div class="hero-shade"></div>

  <svg class="hero-curve" viewBox="0 0 1200 150" preserveAspectRatio="none" aria-hidden="true">
    <path d="M0,25 Q600,200 1200,15 L1200,150 L0,150 Z" fill="#b8946a"/>
    <path d="M0,40 Q600,232 1200,52 L1200,150 L0,150 Z" fill="#ffffff"/>
  </svg>

  <div class="brand">
    <span class="brand-dot"></span>
    <span class="brand-name">The Copperline Collective</span>
  </div>

  <nav class="main-nav">
    <a href="#" class="is-active">HOME</a>
    <a href="#">ABOUT</a>
    <a href="#">WHY US</a>
    <a href="#">SERVICES</a>
    <a href="#">EVENT</a>
    <a href="#">MISSION</a>
    <a href="#">CONTACT</a>
  </nav>

  <svg class="hero-arrow prev" viewBox="0 0 26 58" aria-label="Previous slide"><polyline points="24,2 3,29 24,56" fill="none" stroke="#ffffff" stroke-width="2.5"/></svg>
  <svg class="hero-arrow next" viewBox="0 0 26 58" aria-label="Next slide"><polyline points="2,2 23,29 2,56" fill="none" stroke="#ffffff" stroke-width="2.5"/></svg>

  <h1 class="hero-title">BIG EVENTS FOR FURNITURE STORES</h1>
  <p class="hero-sub">MAECENAS ALIQUET VELIT VEL TURPIS MAURIS NEQUE</p>
</header>

<span class="hero-badge" aria-hidden="true"></span>

<section class="features">
  <article class="card">
    <div class="card-photo showroom" role="img" aria-label="Photo of salespeople in a furniture showroom"></div>
    <h2 class="card-title">OUR VISION</h2>
    <p class="card-text">Morbi diam mauris viverra in gravida eu mattis in ante Morbi eget arcu Morbi porta libero id ullamcorper</p>
    <a href="#" class="btn-pill">READ MORE</a>
  </article>
  <article class="card">
    <div class="card-photo gallery" role="img" aria-label="Photo of a furniture store floor with sofas"></div>
    <h2 class="card-title">WHAT WE DO</h2>
    <p class="card-text">Morbi diam mauris viverra in gravida eu mattis in ante Morbi eget arcu Morbi porta ullamcorper</p>
    <a href="#" class="btn-pill">READ MORE</a>
  </article>
  <article class="card">
    <div class="card-photo dining" role="img" aria-label="Photo of dining tables and chairs on display"></div>
    <h2 class="card-title">WHY US</h2>
    <p class="card-text">Morbi diam mauris viverra in gravida eu mattis in ante Morbi eget arcu Morbi porta libero id ullamcorper</p>
    <a href="#" class="btn-pill">READ MORE</a>
  </article>
</section>

<section class="mission">
  <div class="mission-panel">
    <h2 class="mission-title">OUR MISSION</h2>
    <p class="mission-text first">Praesent elementum elit at tellus nec ultricies sit amet porttitor mattis enim In massa libero interdum nec interdum vel blandit sed nulla In ullamcorper est</p>
    <p class="mission-text second">eget tempor cursus neque mi consectetuer mi a ultricies massa est sed nisl Class aptent taciti sociosqu ad litora torquent per conubia nostra per inceptos hymenaeos Proin nulla arcu nonummy luctus dictum eget fermentum et lorem</p>
    <a href="#" class="btn-outline">READ MORE</a>
  </div>
  <div class="mission-photo" role="img" aria-label="Photo of a cheering crowd with raised hands under stage lights"></div>
</section>
<span class="mission-notch" aria-hidden="true"></span>

<section class="contact" role="img" aria-label="Dark blurred photo of an event hall behind the contact form">
  <h2 class="contact-title">QUICK CONTACT</h2>
  <div class="field col-a row-1">First Name</div>
  <div class="field col-b row-1">Last Name</div>
  <div class="field col-a row-2">Phone</div>
  <div class="field col-b row-2">Email address</div>
  <div class="field message">Message</div>
  <div class="btn-submit">SUBMIT NOW</div>
</section>

<footer class="site-footer">
  <nav class="footer-nav">
    <a href="#">HOME</a>
    <a href="#">ABOUT</a>
    <a href="#">WHY US</a>
    <a href="#">SERVICES</a>
    <a href="#">EVENT</a>
    <a href="#">MISSION</a>
    <a href="#">CONTACT</a>
  </nav>
  <p class="footer-legal">© 2017 Company Name &nbsp;All right reserved &nbsp;Term of Use</p>
  <a href="#" class="social" aria-label="chatterbook">
    <span class="social-label">chatterbook</span>
    <span class="social-ring"></span>
  </a>
</footer>

</body>
</html>
```